Option Sheet

We need a one page option sheet with a left to right reading of the five options. It should be a one sheet, multiple colors and definitive separations between options This is used in a sales consultation. Backround or colors not in option need to have the follow RGB value (5 red, 20 green, 63 blue)

We added a smaller text file, please change that point

Target Market(s)

Divorce

Industry/Entity Type

Legal

Requirements
Must have
• 1) All five options left to right
• 2)language included in sheet

```html
<!DOCTYPE html>
<html lang="en">
<head>
<meta charset="utf-8">
<title>Divorce – Five Options</title>
<link rel="stylesheet" href="https://fonts.googleapis.com/css2?family=Source+Sans+3:wght@400;600;700&display=swap">
<style>
  :root {
    --backdrop: #6d6e71;
    --sheet: #e6e7e8;
    --sheet-band: #f1f2f2;
    --ink: #414042;
    --red: #ef4136;
    --purple: #662d91;
    --orange: #f7941d;
    --green: #006838;
    --blue: #27aae1;
    --white: #ffffff;
  }
  * { box-sizing: border-box; margin: 0; padding: 0; }
  html, body {
    width: 1200px; height: 866px; overflow: hidden;
    background: var(--backdrop);
    font-family: "Source Sans 3", sans-serif;
    color: var(--ink);
  }
  .sheet {
    position: absolute; left: 115px; top: 121px;
    width: 977px; height: 622px;
    background: var(--sheet);
    overflow: hidden;
  }
  .sheet__band {
    position: absolute; left: 0; top: 100px; width: 100%; height: 60px;
    background: linear-gradient(to bottom, var(--sheet-band), var(--sheet));
  }
  .banner { position: absolute; left: 0; top: 0; width: 977px; height: 126px; }
  .banner__title {
    position: absolute; left: 0; top: 26px; width: 100%;
    text-align: center; color: var(--white);
    font-size: 45px; font-weight: 400; letter-spacing: 0.5px;
  }
  .sheet__footer {
    position: absolute; left: 0; bottom: 0; width: 100%; height: 9px;
    background: var(--red);
  }
  .options {
    position: absolute; left: 12px; top: 159px;
    width: 945px; height: 404px;
    display: flex;
  }
  .option {
    flex: 1; position: relative;
    background: linear-gradient(to right, #ffffff 0%, #f4f4f5 70%, #e3e4e5 100%);
    border-bottom: 7px solid var(--accent);
    box-shadow: 2px 0 4px rgba(0,0,0,0.12);
    display: flex; flex-direction: column;
  }
  .option--red { --accent: var(--red); }
  .option--purple { --accent: var(--purple); }
  .option--orange { --accent: var(--orange); }
  .option--green { --accent: var(--green); }
  .option--blue { --accent: var(--blue); }
  .option__head {
    height: 57px; background: var(--accent); color: var(--white);
    text-align: center; padding-top: 10px;
  }
  .option__number { font-size: 14px; font-weight: 700; line-height: 18px; }
  .option__name { font-size: 13px; font-weight: 400; line-height: 18px; }
  .option__body { padding: 10px 8px 0 9px; }
  .option__label {
    color: var(--accent); font-size: 11.5px; font-weight: 700;
    text-align: center; line-height: 14px; margin-bottom: 2px;
  }
  .option__list { list-style: none; font-size: 11px; line-height: 13px; }
  .option__list li {
    padding-left: 8px; text-indent: -8px; margin-bottom: 4px;
  }
  .option__list li::before { content: "• "; }
  .option__divider {
    border: 0; border-top: 1px dotted var(--accent);
    margin: 8px 0 10px; opacity: 0.8;
  }
</style>
</head>
<body>
  <main class="sheet">
    <div class="sheet__band"></div>
    <svg class="banner" viewBox="0 0 977 126" aria-hidden="true">
      <polygon points="0,0 977,0 977,102 488,126 0,102" fill="var(--red)"/>
    </svg>
    <h1 class="banner__title">DIVORCE - FIVE OPTIONS</h1>

    <section class="options">
      <article class="option option--red">
        <header class="option__head">
          <div class="option__number">OPTION #1</div>
          <div class="option__name">Do Nothing</div>
        </header>
        <div class="option__body">
          <h3 class="option__label">ADVANTAGES:</h3>
          <ul class="option__list">
            <li>Stay married</li>
            <li>No life Changes</li>
          </ul>
          <hr class="option__divider">
          <h3 class="option__label">DISADVANTAGES:</h3>
          <ul class="option__list">
            <li>Remain unhappy, depressed, anxious</li>
            <li>Feel unsafe</li>
            <li>Money and assets may disappear</li>
            <li>Spouse may threaten to leave and/or divorce you</li>
            <li>May cause children to be confused, distressed</li>
            <li>What is going to change?</li>
          </ul>
        </div>
      </article>

      <article class="option option--purple">
        <header class="option__head">
          <div class="option__number">OPTION #2</div>
          <div class="option__name">Go to Counseling</div>
        </header>
        <div class="option__body">
          <h3 class="option__label">ADVANTAGES:</h3>
          <ul class="option__list">
            <li>Reconcile marriage</li>
            <li>Help make a better life</li>
          </ul>
          <hr class="option__divider">
          <h3 class="option__label">DISADVANTAGES:</h3>
          <ul class="option__list">
            <li>Past issues are highlighted and may drudge up old wounds</li>
            <li>It may just clarify the reasons you need to separate and/or divorce</li>
            <li>There is no quick fix for any situation and BOTH parties must be invested and willing to participate</li>
            <li>Bringing a third party into the marriage may cause more confusion and possible distrust</li>
          </ul>
        </div>
      </article>

      <article class="option option--orange">
        <header class="option__head">
          <div class="option__number">OPTION #3</div>
          <div class="option__name">Do it Yourself</div>
        </header>
        <div class="option__body">
          <h3 class="option__label">ADVANTAGES:</h3>
          <ul class="option__list">
            <li>No attorney fees</li>
          </ul>
          <hr class="option__divider" style="margin-top:24px">
          <h3 class="option__label">DISADVANTAGES:</h3>
          <ul class="option__list">
            <li>People often find that what is “fair,” may in fact, not be truly fair</li>
            <li>Often times, people do not know the risks</li>
            <li>Complicated legal system</li>
            <li>Unsure how to complete the necessary paperwork and meet the deadlines</li>
            <li>You are too emotional and may be unable to remain clear-headed</li>
            <li>It can be very stressful</li>
          </ul>
        </div>
      </article>

      <article class="option option--green">
        <header class="option__head">
          <div class="option__number">OPTION #4</div>
          <div class="option__name">Limited Representation</div>
        </header>
        <div class="option__body">
          <h3 class="option__label">ADVANTAGES:</h3>
          <ul class="option__list">
            <li>Balance between going alone and our limited involvement in the case</li>
          </ul>
          <h3 class="option__label" style="margin-top:6px">DISADVANTAGES:</h3>
          <ul class="option__list">
            <li>Our terms may not benefit from our legal knowledge</li>
            <li>The legal consequences of your legal documents will not be explained to you so that you can formulate a plan for handling the rest of your case.</li>
            <li>Your spouse or other parties may cause your legal fees to increase significantly without action on your part</li>
          </ul>
        </div>
      </article>

      <article class="option option--blue">
        <header class="option__head">
          <div class="option__number">OPTION #5</div>
          <div class="option__name">Hire Us</div>
        </header>
        <div class="option__body">
          <h3 class="option__label">ADVANTAGES:</h3>
          <ul class="option__list">
            <li>Provide peace of mind</li>
            <li>Often saves you money in the long run</li>
            <li>Can stop problems before they start and advise how actions /events may impact your case</li>
            <li>May be able to come to a settlement agreement sooner</li>
            <li>Lessen the emotional stress of one of the worst things that can happen to a person</li>
            <li>Inform you of your rights and what you are entitled to</li>
            <li>Save you time and energy</li>
            <li>Gain the full benefits of our experience</li>
            <li>Provide a shoulder to lean on and a sounding board</li>
          </ul>
          <h3 class="option__label" style="margin-top:8px">DISADVANTAGES:</h3>
          <ul class="option__list">
            <li>Cost</li>
          </ul>
        </div>
      </article>
    </section>

    <div class="sheet__footer"></div>
  </main>
</body>
</html>
```